I want a modern looking Pulp Book cover.

There is a company called Velvet Gutter press that has incredible covers. And I already have some background art. This is novel with Sex and crime and it should look dangerous and fun. If you don't know what Pulp books are, please google it.

Here is the information needed
Title: Glass Orchids
Author: Lu Vask
Tagline: She made a call of the wild, and danger answered!
(Other optional tagline, instead of author): A Novella by Lu Vask

I have uploaded some art work. you are free to manipulate it anyway you want.

• Must have a proportion of 1 wide and 1 1/2 tall.

Also, if you win the contest, I want the Final files sent to me as AI and PDF.
With all the layers included so I can manipulate as well.

```html
<!DOCTYPE html>
<html lang="en">
<head>
<meta charset="utf-8">
<title>Glass Orchids — A Novella by Lu Vask</title>
<link rel="stylesheet" href="https://fonts.googleapis.com/css2?family=Playfair+Display:wght@700;900&family=Titan+One&family=Roboto+Condensed:wght@700&display=swap">
<style>
  :root {
    --stage: #5e5e5e;
    --night-top: #3a3236;
    --night-mid: #3f4a3e;
    --haze: #5b6a57;
    --street: #4a3a2c;
    --street-dark: #2c231b;
    --title-red: #c23524;
    --title-edge: #f2c23b;
    --band-red: #b5312a;
    --ink-white: #f4f1ea;
  }
  * { box-sizing: border-box; margin: 0; padding: 0; }
  html, body {
    width: 1200px;
    height: 795px;
    overflow: hidden;
    background: var(--stage);
  }
  .stage {
    position: relative;
    width: 1200px;
    height: 795px;
    display: flex;
    align-items: center;
    justify-content: center;
  }
  .cover {
    position: relative;
    width: 500px;
    height: 750px;
    overflow: hidden;
    box-shadow: 0 6px 24px rgba(0,0,0,0.35);
  }
  .cover-art {
    position: absolute;
    inset: 0;
    background:
      radial-gradient(ellipse 60% 18% at 45% 52%, rgba(120,140,110,0.45), transparent 70%),
      linear-gradient(180deg,
        var(--night-top) 0%,
        #3d3a3a 28%,
        var(--night-mid) 45%,
        var(--haze) 55%,
        var(--street) 68%,
        var(--street-dark) 100%);
  }
  .tagline {
    position: absolute;
    top: 58px;
    left: 0;
    width: 100%;
    text-align: center;
    color: var(--ink-white);
    font-family: "Playfair Display", Georgia, serif;
    font-weight: 900;
    text-transform: uppercase;
    text-shadow: 0 2px 4px rgba(0,0,0,0.6);
    line-height: 1.15;
  }
  .tagline-lead { display: block; font-size: 17px; letter-spacing: 0.5px; }
  .tagline-punch { display: block; font-size: 25px; letter-spacing: 0.5px; }
  .title {
    position: absolute;
    left: 90px;
    top: 330px;
    width: 420px;
    transform: rotate(24deg);
    transform-origin: left top;
    font-family: "Titan One", "Arial Black", sans-serif;
    font-size: 76px;
    line-height: 0.9;
    color: var(--title-red);
    -webkit-text-stroke: 3px var(--title-edge);
    paint-order: stroke fill;
    text-transform: uppercase;
    text-shadow: 3px 4px 0 rgba(60,10,5,0.55);
  }
  .title-line { display: block; }
  .title-line + .title-line { padding-left: 14px; }
  .byline {
    position: absolute;
    left: 0;
    bottom: 30px;
    width: 245px;
    height: 34px;
    background: var(--band-red);
    color: var(--ink-white);
    font-family: "Roboto Condensed", "Arial Narrow", sans-serif;
    font-weight: 700;
    font-size: 19px;
    letter-spacing: 0.6px;
    text-transform: uppercase;
    display: flex;
    align-items: center;
    padding-left: 14px;
  }
</style>
</head>
<body>
  <main class="stage">
    <article class="cover">
      <div class="cover-art" role="img" aria-label="Night street illustration: a woman in a red top and jeans walking a small fluffy dog, a man behind her holding a German shepherd on a leash, glowing street lamps in a misty park and a cobbled path"></div>
      <p class="tagline">
        <span class="tagline-lead">She made a call of the wild,</span>
        <span class="tagline-punch">and danger answered!</span>
      </p>
      <h1 class="title">
        <span class="title-line">Glass</span>
        <span class="title-line">Orchids</span>
      </h1>
      <p class="byline">A Novella by Lu Vask</p>
    </article>
  </main>
</body>
</html>
```